WordPress Site That Reviews Footwear

We need a wordpress web design for an affiliate site called PaceKite. We review and do roundups on footwear products. The final design should be clean and mobile friendly. The site should be built with Gutenberg page builder. We like the design of https://lunavessel.com/.
Updates

Need extra days to review

Target Market(s)

USA

Industry/Entity Type

Footwear

Logo Text

PaceKite

Number of Pages Required

4 page

Font styles to use
Serif
Sans Serif

Requirements
Must have
• Wordpress site
Blog post
Page
Categories
Homepage

```html
<!DOCTYPE html>
<html lang="en">
<head>
<meta charset="utf-8">
<title>PaceKite – Footwear Reviews</title>
<link href="https://fonts.googleapis.com/css2?family=Gelasio:wght@700&family=Poppins:wght@400;500;600&display=swap" rel="stylesheet">
<style>
:root{
  --ink:#111;
  --text:#333;
  --muted:#777;
  --green:#9ccc2c;
  --pink:#ec2b7c;
  --mint:#e9f7f6;
  --card-shadow:0 2px 10px rgba(0,0,0,.12);
}
*{margin:0;padding:0;box-sizing:border-box}
html,body{width:1200px;height:3109px;overflow:hidden;background:#fff}
body{position:relative;font-family:'Poppins',sans-serif;color:var(--text)}
.abs{position:absolute}
.serif{font-family:'Gelasio',serif;font-weight:700;color:var(--ink)}

/* nav */
.nav a{position:absolute;top:47px;font-size:11.5px;line-height:14px;color:var(--ink);text-decoration:none;letter-spacing:.2px}
.nav .brand{position:absolute;top:28px;left:0;width:1200px;text-align:center;font-size:44px;line-height:52px}
.nav .social{position:absolute;top:47px;left:988px;font-size:10.5px;line-height:14px;font-weight:600;color:var(--ink);display:flex;gap:7px}

/* hero */
.hero-title{left:142px;top:236px;font-size:84px;line-height:1}
.hero-sub{left:145px;top:358px;font-size:27px;line-height:38px;color:var(--ink)}
.btn{display:flex;align-items:center;justify-content:center;background:var(--green);color:#fff;font-weight:600;border-radius:40px}
.hero-btn{left:145px;top:476px;width:196px;height:66px;font-size:16px}
.hero-photo{left:602px;top:114px;width:596px;height:626px;background:linear-gradient(160deg,#f04d92 0%,#ec2b7c 55%,#f6c5d9 100%)}

/* about */
.section-title{left:0;width:1200px;text-align:center;font-size:46px;line-height:60px}
.about-text{left:170px;top:956px;width:860px;text-align:center;font-size:13px;line-height:30.4px;color:var(--text)}
.feature{width:213px;height:174px;background:#fff;box-shadow:var(--card-shadow);display:flex;flex-direction:column;align-items:center;justify-content:flex-end;padding-bottom:38px}
.feature svg{margin-bottom:18px}
.feature span{font-size:18px;font-weight:500;color:var(--ink)}

/* benefits */
.benefits{left:0;top:1495px;width:797px;height:662px;background:var(--green);border-radius:0 60px 60px 0}
.benefits-title{left:145px;top:1572px;font-size:46px;line-height:60px;color:#fff}
.benefit-title{left:237px;font-size:21px;font-weight:500;color:#fff}
.benefit-text{left:239px;width:300px;font-size:11.5px;line-height:23.5px;color:#fff}
.video{left:547px;top:1614px;width:619px;height:424px;background:linear-gradient(160deg,#0c0c0e 0 55%,#6e6f73 56%,#a4a5a8 100%)}

/* blog */
.post{background:#fff;border:2px solid #ddd;box-shadow:var(--card-shadow)}
.date{width:50px;height:46px;color:#fff;display:flex;flex-direction:column;align-items:center;justify-content:center;line-height:1}
.date b{font-size:21px;font-weight:600}
.date small{font-size:14px}
.post h4{position:absolute;left:81px;font-size:16px;font-weight:500;color:var(--ink);line-height:23px;width:190px}
.post p{position:absolute;left:21px;width:240px;font-size:11.5px;line-height:19.5px;color:var(--muted)}
.post .more{position:absolute;left:21px;font-size:13px;font-weight:600;color:var(--pink)}

/* footer */
.footer{left:0;top:2788px;width:1200px;height:321px;background:var(--mint)}
.f-head{font-size:15px;font-weight:600;color:var(--ink)}
.f-link{font-size:12px;color:var(--muted)}
.pay{width:30px;height:20px;border-radius:3px}
</style>
</head>
<body>

<nav class="nav">
  <a style="left:144px">HOME</a>
  <a style="left:202px">PRODUCTS</a>
  <a style="left:288px">FOOTWEAR</a>
  <a style="left:376px">REVIEWS</a>
  <div class="brand serif">PaceKite</div>
  <a style="left:789px">ABOUT</a>
  <a style="left:851px">CONTACT</a>
  <svg class="abs" style="left:949px;top:45px" width="18" height="18" viewBox="0 0 18 18"><circle cx="7.5" cy="7.5" r="5.5" fill="none" stroke="#111" stroke-width="2.4"/><path d="M12 12l4.5 4.5" stroke="#111" stroke-width="2.6" stroke-linecap="round"/></svg>
  <div class="social"><span>Friendsy</span><span>Chirper</span><span>Linkwork</span></div>
</nav>

<h1 class="abs serif hero-title">PaceKite</h1>
<p class="abs hero-sub">We review and do roundups<br>on footwear products.</p>
<div class="abs btn hero-btn">GET STARTED</div>
<svg class="abs" style="left:145px;top:642px" width="30" height="64" viewBox="0 0 30 64"><rect x="2" y="2" width="26" height="40" rx="13" fill="none" stroke="#111" stroke-width="2"/><path d="M15 10v8" stroke="#111" stroke-width="2" stroke-linecap="round"/><path d="M4 50l11 10 11-10" fill="none" stroke="#111" stroke-width="2"/></svg>

<div class="abs hero-photo" role="img" aria-label="Photo of a pair of grey and white sneakers with pink laces in front of a pink backdrop"></div>

<h2 class="abs serif section-title" style="top:862px">What is PaceKite?</h2>
<p class="abs about-text">Lorem ipsum dolor sit amet, consectetur adipiscing elit, sed do eiusmod tempor incididunt ut labore et dolore magna aliqua. Quis ipsum suspendisse ultrices gravida. Risus commodo viverra maecenas accumsan lacus vel facilisorem ipsum dolor sit aonsectetur adipiscing elit, sed do eiusmod tempor incididunt ut labore et dolore magna aliquis ipsum suspendisse ultrices gravidaisus commodo viverra maecenas accumsan lacus vel facilisis. Lorem ipsum dolor sit amet, consectetur adipiscid do eiusmod tempor incididunt ut labore et dolore magnais ipsum susmodo viverra maecenas accumsan lacus vel facilisis.</p>

<div class="abs feature" style="left:143px;top:1185px">
  <svg width="72" height="72" viewBox="0 0 72 72" fill="none" stroke="#ec2b7c" stroke-width="2.4"><path d="M4 68V52c8 0 14-4 20-12l20-28c6-8 14-8 16 2l-2 56H48V40l-8 20c-2 6-6 8-12 8z"/><path d="M50 40v28"/></svg>
  <span>Sed erspiciatis</span>
</div>
<div class="abs feature" style="left:376px;top:1210px">
  <svg width="80" height="72" viewBox="0 0 80 72" fill="none" stroke="#ec2b7c" stroke-width="2.2"><rect x="6" y="4" width="68" height="48"/><path d="M16 16h48M16 26h30M16 36h24"/><circle cx="54" cy="42" r="9"/><path d="M48 50v18l6-5 6 5V50"/></svg>
  <span>Quis nostrum</span>
</div>
<div class="abs feature" style="left:608px;top:1185px">
  <svg width="76" height="72" viewBox="0 0 76 72" fill="none" stroke="#ec2b7c" stroke-width="2.4"><path d="M4 30l26-26 12 10-6 8 12 10 14 8c6 4 10 10 10 18v4H50z"/><path d="M22 40l-8 8M30 48l-8 8M50 60h22"/></svg>
  <span>Duis aute irur</span>
</div>
<div class="abs feature" style="left:840px;top:1210px">
  <svg width="72" height="72" viewBox="0 0 72 72" fill="none" stroke="#ec2b7c" stroke-width="2.2"><rect x="8" y="4" width="60" height="28" rx="3"/><path d="M20 12l2 4h4l-3 3 1 4-4-2-4 2 1-4-3-3h4zM38 12l2 4h4l-3 3 1 4-4-2-4 2 1-4-3-3h4zM56 12l2 4h4l-3 3 1 4-4-2-4 2 1-4-3-3h4z"/><rect x="4" y="44" width="10" height="24"/><path d="M14 46l10-10 4-10c4 0 6 4 4 10h14c4 0 4 6 0 6 4 0 4 6 0 6 4 0 4 6 0 6 3 0 3 6-1 6H14"/></svg>
  <span>Nemo enim ipsa</span>
</div>

<div class="abs benefits"></div>
<h2 class="abs serif benefits-title">Benefits</h2>

<svg class="abs" style="left:145px;top:1680px" width="68" height="60" viewBox="0 0 68 60" fill="none" stroke="#fff" stroke-width="2"><rect x="22" y="2" width="40" height="24"/><path d="M30 18l8-10M44 10h12M44 16h12M44 22h10"/><path d="M2 58V34l14-8 10 8 10 4 20 4c6 2 10 8 10 16z"/><path d="M2 50h64"/></svg>
<div class="abs benefit-title" style="top:1674px">Nemo enim ipsa</div>
<p class="abs benefit-text" style="top:1714px">Lorem ipsum dolor sit amet, consectdipiscing elit, sed do eiusmod tempor incididunt ut labore et dolore magna aliqis ipsum suspendisse</p>

<svg class="abs" style="left:145px;top:1826px" width="60" height="60" viewBox="0 0 60 60" fill="none" stroke="#fff" stroke-width="2"><path d="M30 2l7 5 8-1 4 7 7 4-1 8 5 5-5 5 1 8-7 4-4 7-8-1-7 5-7-5-8 1-4-7-7-4 1-8-5-5 5-5-1-8 7-4 4-7 8 1z"/><circle cx="30" cy="30" r="14"/><path d="M23 30l5 5 10-10"/></svg>
<div class="abs benefit-title" style="top:1818px">Quis autem vel eum</div>
<p class="abs benefit-text" style="top:1858px">Lorem ipsum dolor sit amet, consectdipiscing elit, sed do eiusmod tempor incididunt ut labore et dolore magna aliqis ipsum suspendisse</p>

<svg class="abs" style="left:145px;top:1966px" width="66" height="66" viewBox="0 0 66 66" fill="none" stroke="#fff" stroke-width="2"><rect x="3" y="3" width="26" height="60" rx="13"/><rect x="37" y="3" width="26" height="60" rx="13"/><path d="M3 18h26M37 18h26"/><circle cx="16" cy="26" r="4"/><circle cx="50" cy="26" r="4"/></svg>
<div class="abs benefit-title" style="top:1962px">Nemo enim ipsa</div>
<p class="abs benefit-text" style="top:2002px">Lorem ipsum dolor sit amet, consectdipiscing elit, sed do eiusmod tempor incididunt ut labore et dolore magna aliqis ipsum suspendisse</p>

<div class="abs video" role="img" aria-label="Video still of a grey knit running shoe with orange accents on a dark and grey background"></div>
<svg class="abs" style="left:772px;top:1742px" width="168" height="168" viewBox="0 0 168 168" fill="none" stroke="#fff" stroke-width="8"><path d="M84 6a78 78 0 1 1-72 48"/><path d="M66 52v64l50-32z" stroke-linejoin="round"/></svg>

<h2 class="abs serif section-title" style="top:2252px">Learn from the Blog</h2>

<svg class="abs" style="left:56px;top:2510px" width="34" height="66" viewBox="0 0 34 66" fill="none" stroke="#444" stroke-width="1.6"><path d="M32 2L2 33l30 31"/></svg>
<svg class="abs" style="left:1110px;top:2510px" width="34" height="66" viewBox="0 0 34 66" fill="none" stroke="#444" stroke-width="1.6"><path d="M2 2l30 31L2 64"/></svg>

<article class="abs post" style="left:155px;top:2448px;width:278px;height:187px">
  <div class="abs date" style="left:21px;top:22px;background:var(--green)"><b>02</b><small>JAN</small></div>
  <h4 style="top:20px">Pellentesque faucibus Ut accumsan ultric</h4>
  <p style="top:80px">Duis quam Nam eget lacus Aliquam erat volutpat Quisque dignissim congue leovel lacus vitae felis vestibulum</p>
  <span class="more" style="top:146px">READ MORE</span>
</article>

<article class="abs post" style="left:461px;top:2368px;width:278px;height:330px">
  <div class="abs" style="left:6px;top:6px;width:262px;height:140px;background:linear-gradient(120deg,#f0a41c,#e88f12)" role="img" aria-label="Photo of a woman in a polka dot dress holding up a pair of white sneakers on an orange background"></div>
  <div class="abs date" style="left:21px;top:164px;background:var(--pink)"><b>02</b><small>JAN</small></div>
  <h4 style="top:162px">Pellentesque faucibus Ut accumsan ultric</h4>
  <p style="top:222px">Duis quam Nam eget lacus Aliquam erat volutpat Quisque dignissim congue leovel lacus vitae felis vestibulum</p>
  <span class="more" style="top:288px">READ MORE</span>
</article>

<article class="abs post" style="left:766px;top:2448px;width:278px;height:187px">
  <div class="abs date" style="left:21px;top:22px;background:var(--green)"><b>02</b><small>JAN</small></div>
  <h4 style="top:20px">Pellentesque faucibus Ut accumsan ultric</h4>
  <p style="top:80px">Duis quam Nam eget lacus Aliquam erat volutpat Quisque dignissim congue leovel lacus vitae felis vestibulum</p>
  <span class="more" style="top:146px">READ MORE</span>
</article>

<footer class="abs footer">
  <div class="abs f-head" style="left:177px;top:82px">ABOUT</div>
  <div class="abs f-link" style="left:177px;top:122px">About</div>
  <div class="abs f-link" style="left:177px;top:155px">Contact</div>
  <div class="abs f-link" style="left:177px;top:188px">Media</div>

  <div class="abs f-head" style="left:328px;top:82px">COMPANY</div>
  <div class="abs f-link" style="left:328px;top:122px">Terms of Use</div>
  <div class="abs f-link" style="left:328px;top:155px">Privacy Policy</div>
  <div class="abs f-link" style="left:328px;top:188px">How We Make Money</div>

  <div class="abs f-head" style="left:545px;top:82px">SIGN UP NEWSLETTER</div>
  <div class="abs f-link" style="left:545px;top:122px">Sed ut perspiciatis unde omnis iste natus</div>
  <div class="abs" style="left:546px;top:144px;width:252px;height:46px;border-radius:24px;background:#fff;box-shadow:0 2px 6px rgba(0,0,0,.1)"></div>
  <div class="abs" style="left:571px;top:161px;font-size:9.5px;color:#333">Enter Email</div>
  <div class="abs btn" style="left:698px;top:144px;width:100px;height:46px;font-size:14px">SIGN UP</div>

  <div class="abs f-head" style="left:912px;top:82px">SOCIAL MEDIA</div>
  <div class="abs" style="left:913px;top:124px;width:11px;height:11px;border-radius:2px;background:var(--pink)"></div>
  <div class="abs f-link" style="left:941px;top:122px">Friendsy</div>
  <div class="abs" style="left:913px;top:157px;width:11px;height:11px;border-radius:2px;background:var(--pink)"></div>
  <div class="abs f-link" style="left:941px;top:155px">Chirper</div>
  <div class="abs" style="left:913px;top:190px;width:11px;height:11px;border-radius:2px;background:var(--pink)"></div>
  <div class="abs f-link" style="left:941px;top:188px">Linkwork</div>

  <div class="abs" style="left:177px;top:266px;font-size:11px;color:var(--muted)">© 2021 PaceKite.All Rights Reserved | &nbsp;Privacy Policy &nbsp;| Terms and Conditons</div>
  <div class="abs pay" style="left:830px;top:264px;background:#dfe3ec"></div>
  <div class="abs pay" style="left:870px;top:264px;background:#f3c7a0"></div>
  <div class="abs pay" style="left:910px;top:264px;background:#e6e6e6"></div>
  <div class="abs pay" style="left:950px;top:264px;background:#6fa0d4"></div>
  <div class="abs pay" style="left:990px;top:264px;background:#f4e6a6"></div>
</footer>

</body>
</html>
```